Business Card Design for Occupational Medicine Start Up Company

We need to design a professional business card. We are a healthcare company providing occupational medicine services to blue collar industries. We are professional, efficient and high quality service providers.

Target Market(s)

Blue Collar Industry: Shipbuilding, Ports, Trucking Companies; The Executives and Safety Officers for these companies

Industry/Entity Type

Healthcare

Contact Information for Business Card

Logo, Name, Title, Email, Phone

Other font styles liked:
• Please match our Brand Guide

Requirements
Must have
• Our Company Colors and Logo

```html
<!DOCTYPE html>
<html lang="en">
<head>
<meta charset="utf-8">
<title>HarborCare Clinics – Business Card</title>
<link href="https://fonts.googleapis.com/css2?family=Montserrat:wght@400;600;700&display=swap" rel="stylesheet">
<style>
  :root {
    --board: #e6e6e6;
    --card: #ffffff;
    --orange: #f0b254;
    --navy: #2b3580;
    --cyan: #27a3dd;
    --ink: #2a2a2a;
  }
  * { box-sizing: border-box; margin: 0; padding: 0; }
  html, body { width: 731px; height: 1200px; overflow: hidden; }
  body {
    position: relative;
    background: var(--board);
    font-family: "Montserrat", sans-serif;
    color: var(--ink);
  }
  .brand-lockup {
    position: absolute;
    top: 62px; left: 0; width: 731px;
    display: flex; align-items: center; justify-content: center; gap: 16px;
  }
  .brand-dot { border-radius: 50%; background: var(--orange); flex: none; }
  .brand-lockup .brand-dot { width: 72px; height: 72px; }
  .brand-name {
    font-weight: 600; text-align: center; line-height: 1.1;
    text-transform: uppercase;
  }
  .brand-lockup .brand-name { color: var(--navy); font-size: 29px; }
  .brand-name .sub { display: block; letter-spacing: 0.28em; font-size: 0.5em; margin-top: 4px; }

  .card {
    position: absolute; top: 674px;
    width: 266px; height: 466px;
    background: var(--card); overflow: hidden;
  }
  .card-front { left: 70px; }
  .card-back { left: 395px; }
  .card svg.shapes { position: absolute; inset: 0; }

  .card .brand {
    position: absolute; left: 0; width: 266px;
    display: flex; flex-direction: column; align-items: center; gap: 14px;
  }
  .card .brand-dot { width: 60px; height: 60px; }
  .card .brand-name { color: var(--cyan); font-size: 17px; }
  .card-front .brand { top: 175px; }
  .card-back .brand { top: 85px; }

  .person { position: absolute; left: 23px; top: 270px; }
  .person-name { color: var(--cyan); font-weight: 700; font-size: 17px; letter-spacing: 0.01em; }
  .person-title { font-size: 12.5px; letter-spacing: 0.03em; margin-top: 2px; }

  .contacts { position: absolute; left: 24px; top: 387px; list-style: none; }
  .contacts li {
    display: flex; align-items: center; gap: 5px;
    font-size: 9.6px; height: 13.8px; letter-spacing: 0.02em;
  }
  .contacts svg { width: 8px; height: 8px; flex: none; }
</style>
</head>
<body>

<header class="brand-lockup">
  <span class="brand-dot"></span>
  <span class="brand-name">HarborCare<span class="sub">Clinics</span></span>
</header>

<section class="card card-front">
  <svg class="shapes" viewBox="0 0 266 466" aria-hidden="true">
    <path d="M0 0 H221 C150 30 60 50 0 140 Z" fill="var(--orange)"/>
    <path d="M266 325 C200 390 140 420 44 466 H266 Z" fill="var(--navy)"/>
  </svg>
  <div class="brand">
    <span class="brand-dot"></span>
    <span class="brand-name">HarborCare<span class="sub">Clinics</span></span>
  </div>
</section>

<section class="card card-back">
  <svg class="shapes" viewBox="0 0 266 466" aria-hidden="true">
    <path d="M43 0 H266 V140 C230 80 200 40 130 30 C90 25 60 15 43 0 Z" fill="var(--orange)"/>
  </svg>
  <div class="brand">
    <span class="brand-dot"></span>
    <span class="brand-name">HarborCare<span class="sub">Clinics</span></span>
  </div>
  <div class="person">
    <p class="person-name">DANIEL R. CARVER</p>
    <p class="person-title">Chief Executive Manager</p>
  </div>
  <ul class="contacts">
    <li><svg viewBox="0 0 8 8"><rect width="8" height="8" rx="1" fill="var(--orange)"/><path d="M2 2 L3 2 L3.6 3.2 L3 3.7 Q3.7 4.6 4.4 5 L4.8 4.4 L6 5 L6 6 Q3 6 2 2 Z" fill="#fff"/></svg>+1 757-555-0142</li>
    <li><svg viewBox="0 0 8 8"><rect width="8" height="8" rx="1" fill="var(--orange)"/><rect x="1.8" y="2.5" width="4.4" height="3" fill="#fff"/></svg>info@harborcareclinics.com</li>
    <li><svg viewBox="0 0 8 8"><rect width="8" height="8" rx="1" fill="var(--orange)"/><circle cx="4" cy="4" r="2" fill="none" stroke="#fff" stroke-width="0.8"/></svg>harborcareclinics.com</li>
    <li><svg viewBox="0 0 8 8"><rect width="8" height="8" rx="1" fill="var(--orange)"/><path d="M4 6.5 L2.5 4 A1.6 1.6 0 1 1 5.5 4 Z" fill="#fff"/></svg>2875 Dockside Ave Norfolk, VA 23510</li>
  </ul>
</section>

</body>
</html>
```